Business Card Design

We are a residential half way house for the addict ,the alcoholic and dual diagnosed in recovery.
i house both men and woman age 18+

Industry/Entity Type

Residential

```html
<!DOCTYPE html>
<html lang="en">
<head>
<meta charset="utf-8">
<title>Meredith's Family Sober House – Business Card</title>
<link href="https://fonts.googleapis.com/css2?family=Archivo+Black&family=Roboto:wght@300;400&display=swap" rel="stylesheet">
<style>
  :root {
    --backdrop: #e9e5df;
    --card-white: #ffffff;
    --ink: #111111;
    --amber: #e08a1e;
    --night: #0b0806;
    --glow: #7a4a1c;
    --violet: #4a1630;
  }
  * { box-sizing: border-box; margin: 0; padding: 0; }
  html, body { width: 1200px; height: 892px; overflow: hidden; }
  body {
    background: var(--backdrop);
    display: flex;
    align-items: center;
    justify-content: center;
    font-family: "Roboto", Arial, sans-serif;
    color: var(--ink);
  }
  .business-card {
    position: relative;
    width: 476px;
    height: 834px;
    background: var(--card-white);
    box-shadow: 0 6px 24px rgba(0,0,0,0.18);
    overflow: hidden;
  }
  .card-details {
    position: absolute;
    top: 48px;
    right: 34px;
    left: 34px;
    text-align: right;
  }
  .company-name {
    font-family: "Archivo Black", "Arial Black", sans-serif;
    font-size: 31px;
    line-height: 1.02;
    letter-spacing: -0.5px;
  }
  .person-name {
    margin-top: 14px;
    font-weight: 300;
    font-size: 46px;
    line-height: 1.1;
  }
  .person-role { font-size: 17px; font-weight: 400; margin-top: 2px; }
  .person-note { font-size: 16px; font-weight: 400; }
  .contact-list {
    list-style: none;
    margin-top: 40px;
    font-size: 20px;
    font-weight: 400;
    line-height: 1.22;
  }
  .contact-list li {
    display: flex;
    justify-content: flex-end;
    align-items: center;
    gap: 10px;
  }
  .contact-icon { width: 20px; height: 20px; flex: none; }
  .card-footer {
    position: absolute;
    left: 0;
    bottom: 0;
    width: 476px;
    height: 380px;
  }
</style>
</head>
<body>
  <article class="business-card">
    <div class="card-details">
      <h1 class="company-name">Meredith's<br>Family Sober House Inc</h1>
      <p class="person-name">Dana Whitfield</p>
      <p class="person-role">Owner</p>
      <p class="person-note">(15 yrs.in recovery)</p>
      <ul class="contact-list">
        <li>(555) 014-0305
          <svg class="contact-icon" viewBox="0 0 20 20"><rect width="20" height="20" rx="4" fill="#111"/><path d="M6 4.5l2 .3.8 3-1.3 1a7 7 0 0 0 4 4l1-1.3 3 .8.3 2c-.2.8-1 1.3-2 1.2C9 15.7 4.3 11 4.3 6.5c0-1 .5-1.8 1.7-2z" fill="#fff"/></svg>
        </li>
        <li>(555) 014-0306
          <svg class="contact-icon" viewBox="0 0 20 20"><rect width="20" height="20" rx="4" fill="#111"/><path d="M6 4.5l2 .3.8 3-1.3 1a7 7 0 0 0 4 4l1-1.3 3 .8.3 2c-.2.8-1 1.3-2 1.2C9 15.7 4.3 11 4.3 6.5c0-1 .5-1.8 1.7-2z" fill="#fff"/></svg>
        </li>
        <li>(555) 014-5536
          <svg class="contact-icon" viewBox="0 0 20 20"><rect width="20" height="20" rx="4" fill="#111"/><rect x="6" y="4" width="8" height="4" fill="#fff"/><rect x="4" y="8" width="12" height="6" rx="1" fill="#fff"/><rect x="6.5" y="12" width="7" height="4" fill="#fff" stroke="#111" stroke-width="1"/></svg>
        </li>
        <li>dana.whitfield@example.com
          <svg class="contact-icon" viewBox="0 0 20 20"><rect width="20" height="20" rx="4" fill="#111"/><rect x="4" y="6" width="12" height="8.5" fill="#fff"/><path d="M4 6l6 5 6-5" fill="none" stroke="#111" stroke-width="1.2"/></svg>
        </li>
        <li>2418 Palmetto Rd. Seabrook,Fla 33400
          <svg class="contact-icon" viewBox="0 0 20 20"><rect width="20" height="20" rx="4" fill="#111"/><path d="M10 3.5a4.5 4.5 0 0 1 4.5 4.5c0 3.2-4.5 8.5-4.5 8.5S5.5 11.2 5.5 8A4.5 4.5 0 0 1 10 3.5z" fill="#fff"/><circle cx="10" cy="8" r="1.7" fill="#111"/></svg>
        </li>
      </ul>
    </div>

    <svg class="card-footer" viewBox="0 0 476 380" aria-hidden="false">
      <defs>
        <radialGradient id="lantern-night" cx="45%" cy="55%" r="70%">
          <stop offset="0" stop-color="var(--glow)"/>
          <stop offset="0.35" stop-color="var(--violet)"/>
          <stop offset="1" stop-color="var(--night)"/>
        </radialGradient>
      </defs>
      <path class="accent-curve" d="M0 26 Q200 -8 476 96 L476 380 L0 380 Z" fill="var(--amber)"/>
      <path class="footer-photo" role="img" aria-label="Photo of glowing paper sky lanterns rising over a crowd at night" d="M0 40 Q200 6 476 110 L476 380 L0 380 Z" fill="url(#lantern-night)"/>
    </svg>
  </article>
</body>
</html>
```